Brivolt Technologies business card design

We need a business card designed with our new logo. it would be great if the card could communicate it is a technology based company.

Target Market(s)

system integrators

Industry/Entity Type

technology, IOT

Contact Information for Business Card

Name, designation, Address, telephone number, email address

Requirements
Must have
• logo and company name
Nice to have
• something to do with technology

```html
<!DOCTYPE html>
<html lang="en">
<head>
<meta charset="utf-8">
<title>Brivolt Technologies – Business Card</title>
<link rel="stylesheet" href="https://fonts.googleapis.com/css2?family=Exo+2:wght@600&family=Roboto+Condensed:wght@300;400&display=swap">
<style>
  :root {
    --bg: #e4e4e4;
    --card-white: #f7f7f7;
    --ink: #4a4a4c;
    --ink-soft: #5a5a5c;
    --accent: #ef8a1c;
    --band: #3c3c3f;
    --divider: #c9c9c9;
    --card-dark-top: #4a4a4d;
    --card-dark-bottom: #3b3b3e;
    --emboss: #2f2f32;
  }
  * { box-sizing: border-box; margin: 0; padding: 0; }
  html, body { width: 1200px; height: 1200px; overflow: hidden; }
  body { background: var(--bg); position: relative; font-family: "Roboto Condensed", sans-serif; }

  .card {
    position: absolute;
    left: 257px;
    width: 686px;
    height: 392px;
    border-radius: 22px;
    overflow: hidden;
  }
  .card--front { top: 165px; background: var(--card-white); }
  .card--back {
    top: 653px;
    background: linear-gradient(180deg, var(--card-dark-top), var(--card-dark-bottom));
  }

  .brand {
    position: absolute;
    display: flex;
    align-items: center;
    gap: 12px;
    font-family: "Exo 2", sans-serif;
    font-weight: 600;
    color: var(--ink);
  }
  .brand__square { width: 22px; height: 22px; background: var(--accent); flex: none; }
  .brand__name { display: flex; flex-direction: column; line-height: 1; }
  .brand__word { font-size: 44px; letter-spacing: 1px; }
  .brand__sub { font-size: 14px; letter-spacing: 6.2px; margin-top: 6px; }

  .card--front .brand { left: 80px; top: 146px; }

  .divider {
    position: absolute;
    left: 375px; top: 66px;
    width: 1px; height: 219px;
    background: var(--divider);
  }

  .contact { position: absolute; left: 400px; top: 76px; color: var(--ink-soft); }
  .contact__name {
    font-family: "Exo 2", sans-serif;
    font-weight: 600;
    font-size: 25px;
    color: var(--accent);
    line-height: 1.1;
  }
  .contact__role { font-size: 18px; font-weight: 300; margin-top: 1px; }
  .contact__address { font-size: 18px; font-weight: 300; line-height: 22px; margin-top: 12px; }
  .contact__list { list-style: none; margin-top: 9px; }
  .contact__item {
    display: flex; align-items: center; gap: 12px;
    font-size: 18px; font-weight: 300; line-height: 21.5px;
  }
  .contact__item svg { width: 15px; height: 15px; flex: none; fill: var(--accent); }

  .band {
    position: absolute;
    left: 0; top: 330px;
    width: 100%; height: 34px;
    background: var(--band);
    color: #ececec;
    font-size: 17px;
    letter-spacing: 3.4px;
    font-weight: 400;
    display: flex; align-items: center; justify-content: center;
  }
  .band__square {
    position: absolute;
    left: 568px; top: 8px;
    width: 18px; height: 18px;
    background: var(--accent);
  }

  .card--back .brand {
    left: 50%; top: 50%;
    transform: translate(-50%, -50%);
    color: var(--emboss);
  }
  .card--back .brand__word { font-size: 56px; }
  .card--back .brand__sub { font-size: 18px; letter-spacing: 7.6px; }
</style>
</head>
<body>

<section class="card card--front" aria-label="Business card front">
  <div class="brand">
    <span class="brand__square"></span>
    <div class="brand__name">
      <span class="brand__word">BRIVOLT</span>
      <span class="brand__sub">TECHNOLOGIES</span>
    </div>
  </div>

  <div class="divider"></div>

  <div class="contact">
    <h1 class="contact__name">Daniel Morrow</h1>
    <p class="contact__role">Managing Director</p>
    <p class="contact__address">4120 Juniper Court<br>Fairbanks, Alaska 34580</p>
    <ul class="contact__list">
      <li class="contact__item">
        <svg viewBox="0 0 24 24" aria-hidden="true"><path d="M6.6 10.8a15.1 15.1 0 0 0 6.6 6.6l2.2-2.2a1 1 0 0 1 1-.25 11.4 11.4 0 0 0 3.6.57 1 1 0 0 1 1 1V20a1 1 0 0 1-1 1A17 17 0 0 1 3 4a1 1 0 0 1 1-1h3.5a1 1 0 0 1 1 1c0 1.25.2 2.45.57 3.6a1 1 0 0 1-.25 1z"/></svg>
        936-555-0142
      </li>
      <li class="contact__item">
        <svg viewBox="0 0 24 24" aria-hidden="true"><path d="M7 1h10a2 2 0 0 1 2 2v18a2 2 0 0 1-2 2H7a2 2 0 0 1-2-2V3a2 2 0 0 1 2-2zm0 3v14h10V4zm5 15.5a1 1 0 1 0 0 2 1 1 0 0 0 0-2z"/></svg>
        936-555-0187
      </li>
      <li class="contact__item">
        <svg viewBox="0 0 24 24" aria-hidden="true"><path d="M2 5h20v14H2zm2 2v.5l8 5 8-5V7zm0 2.8V17h16V9.8l-8 5z"/></svg>
        info@brivolt.com
      </li>
      <li class="contact__item">
        <svg viewBox="0 0 24 24" aria-hidden="true"><path d="M12 2a10 10 0 1 0 0 20 10 10 0 0 0 0-20zm-1 17.9A8 8 0 0 1 4.2 10.2L9 15v1a2 2 0 0 0 2 2zm6.9-2.5A2 2 0 0 0 16 16h-1v-3a1 1 0 0 0-1-1H8v-2h2a1 1 0 0 0 1-1V7h2a2 2 0 0 0 2-2v-.4a8 8 0 0 1 2.9 12.8z"/></svg>
        www.brivolt.com
      </li>
    </ul>
  </div>

  <div class="band">
    www.brivolt.com
    <span class="band__square"></span>
  </div>
</section>

<section class="card card--back" aria-label="Business card back">
  <div class="brand">
    <span class="brand__square" style="background: var(--emboss); width: 28px; height: 28px;"></span>
    <div class="brand__name">
      <span class="brand__word">BRIVOLT</span>
      <span class="brand__sub">TECHNOLOGIES</span>
    </div>
  </div>
</section>

</body>
</html>
```